Coastline Premier Retreats Business Card Design

Design a business card for Coastline Premier Retreats. Look at the website for colors and reference. Card should have logo, name, title, office number, mobile number, email, URL and a tagline like, "Luxury Hotel & Resort Email Marketing" (This might change).

https://www.coastlinepremierretreats.example

The rest I will leave up to your imagination.

Contact Information for Business Card

Logo, name, title, office number, mobile number, email, URL and a tagline like, "Luxury Hotel & Resort Email Marketing" (This might change).

```html
<!DOCTYPE html>
<html lang="en">
<head>
<meta charset="utf-8">
<title>Coastline Premier Retreats – Business Card</title>
<link href="https://fonts.googleapis.com/css2?family=Arimo:wght@400;700&display=swap" rel="stylesheet">
<style>
  :root {
    --orange: #f07423;
    --black: #1a1a1a;
    --white: #ffffff;
    --backdrop: #e4e4e4;
    --ink: #111111;
  }
  * { margin: 0; padding: 0; box-sizing: border-box; }
  html, body { width: 1200px; height: 998px; overflow: hidden; }
  body {
    background: var(--backdrop);
    font-family: "Arimo", Arial, sans-serif;
    position: relative;
  }
  .card {
    position: absolute;
    left: 250px;
    width: 700px;
    height: 400px;
    overflow: hidden;
  }
  .card-front { top: 60px; background: var(--orange); }
  .card-back { top: 540px; background: var(--white); }

  /* front */
  .front-brand {
    position: absolute;
    inset: 0;
    display: flex;
    align-items: center;
    justify-content: center;
    gap: 16px;
  }
  .brand-square {
    width: 30px; height: 30px;
    background: var(--white);
  }
  .front-brand .brand-name {
    color: var(--white);
    font-weight: 700;
    font-size: 34px;
    letter-spacing: 1px;
    text-transform: uppercase;
  }

  /* back */
  .back-brand {
    position: absolute;
    left: 48px; top: 54px;
    display: flex; align-items: center; gap: 10px;
  }
  .back-brand .brand-square { width: 16px; height: 16px; background: var(--orange); }
  .back-brand .brand-name {
    color: var(--ink);
    font-weight: 700;
    font-size: 17px;
    text-transform: uppercase;
    letter-spacing: .5px;
  }
  .person {
    position: absolute;
    right: 48px; top: 48px;
    text-align: right;
  }
  .person-name {
    color: var(--orange);
    font-weight: 700;
    font-size: 24px;
    letter-spacing: .5px;
  }
  .person-title { color: var(--ink); font-size: 15px; margin-top: 2px; }
  .tagline {
    position: absolute;
    right: 48px; top: 205px;
    text-align: right;
    color: var(--ink);
    font-size: 16px;
    line-height: 1.25;
  }
  .contact-list {
    position: absolute;
    left: 110px; top: 228px;
    list-style: none;
    color: var(--ink);
    font-size: 16px;
    line-height: 24px;
  }
  .contact-list li { display: flex; align-items: center; gap: 8px; }
  .contact-list svg { width: 14px; height: 14px; flex: none; }
  .card-bands { position: absolute; left: 0; bottom: 0; width: 700px; height: 110px; }
  .web-address {
    position: absolute;
    right: 16px; top: 322px;
    color: var(--white);
    font-size: 12.5px;
  }
</style>
</head>
<body>

<section class="card card-front" aria-label="Card front">
  <div class="front-brand">
    <span class="brand-square"></span>
    <span class="brand-name">Coastline Premier Retreats</span>
  </div>
</section>

<section class="card card-back" aria-label="Card back">
  <div class="back-brand">
    <span class="brand-square"></span>
    <span class="brand-name">Coastline Premier Retreats</span>
  </div>

  <div class="person">
    <p class="person-name">DANIEL WHITMORE</p>
    <p class="person-title">Co-Founder</p>
  </div>

  <p class="tagline">Luxury Hotel &amp; Resort<br>Email Marketing</p>

  <ul class="contact-list">
    <li>
      <svg viewBox="0 0 14 14" aria-hidden="true"><path fill="#f07423" d="M1 4c0-2 2-3 6-3s6 1 6 3v1H10V4H4v1H1zM3 6h8l2 7H1z"/></svg>
      555-210-4836
    </li>
    <li>
      <svg viewBox="0 0 14 14" aria-hidden="true"><rect x="3.5" y="1" width="7" height="12" rx="1.5" fill="none" stroke="#f07423" stroke-width="1.4"/><circle cx="7" cy="11" r=".8" fill="#f07423"/></svg>
      555-318-7290
    </li>
    <li>
      <svg viewBox="0 0 14 14" aria-hidden="true"><rect x="1" y="3" width="12" height="8" fill="#f07423"/><path d="M1 3l6 5 6-5" fill="none" stroke="#fff" stroke-width="1"/></svg>
      info@coastlinepremierretreats.example
    </li>
  </ul>

  <svg class="card-bands" viewBox="0 290 700 110" aria-hidden="true">
    <rect x="0" y="346" width="438" height="5" fill="#f07423"/>
    <rect x="0" y="356" width="430" height="44" fill="#1a1a1a"/>
    <polygon points="458,300 700,300 700,400 436,400" fill="#f07423"/>
  </svg>
  <p class="web-address">www.coastlinepremierretreats.example</p>
</section>

</body>
</html>
```